Kelvaro.ch is looking for business card letterhead and envelope C5 with WOW effect

We need a strong business card for our company Kelvaro.ch, logo is available. You want a black or dark background on which the logo Stark r% 26 # 252; appears. Letterhead and envelope in C5 format should be in a similar design, but does not have to be We need a strong business card for our company Kelvaro.ch, logo is available. A black or dark background is desired, on which the logo Stark comes across. The letterhead and the envelope in C5 format should have a similar design.

Target Market(s)

Private customers as well as entrepreneurs

Contact Information for Business Card

E-mail: info@kelvaro-example.ch
Web.www.Kelvaro-example.ch
Tel: +41 ( 0 ) 79 482 6037
Adresse:
Lindenweg 14
9406 Tarnbach

Hier kann man Icons verwenden für Email,Tel und Adressse

Font styles to use
Other font styles liked:
• Dubai,bold

Colors

Designer to choose colors to be used in the design.

Requirements
Must have
• WOW effect
Nice to have
• R% 26 # 252; back business card with our service listings. - VEHICLE LABELING - SHOP WINDOW LABELING - STICKERS AND MUCH MORE ... in red color

```html
<!DOCTYPE html>
<html lang="en">
<head>
<meta charset="utf-8">
<title>Kelvaro.ch – Business Card</title>
<link rel="stylesheet" href="https://fonts.googleapis.com/css2?family=Ubuntu:wght@400;500;700&display=swap">
<style>
  :root {
    --stage: #161616;
    --stage-glow: #2c2c2c;
    --card: #262626;
    --card-edge: #1e1e1e;
    --ink: #ffffff;
    --accent: #fcc61a;
    --service-red: #e0202a;
    --muted: #e6e6e6;
  }
  * { box-sizing: border-box; margin: 0; padding: 0; }
  html, body {
    width: 1200px; height: 900px; overflow: hidden;
  }
  body {
    background: radial-gradient(ellipse at 60% 35%, var(--stage-glow), var(--stage) 70%);
    font-family: "Ubuntu", sans-serif;
    color: var(--ink);
    position: relative;
  }
  .card {
    position: absolute;
    left: 290px;
    width: 620px;
    height: 400px;
    background: linear-gradient(135deg, var(--card-edge), var(--card) 55%, #303030);
    box-shadow: 0 14px 30px rgba(0,0,0,.55);
  }
  .card--back { top: 30px; }
  .card--front { top: 470px; }

  /* Wordmark */
  .wordmark {
    display: flex; align-items: center; gap: 14px;
    font-weight: 700; letter-spacing: 2px; text-transform: uppercase;
    color: var(--ink);
  }
  .wordmark__dot {
    width: 22px; height: 22px; border-radius: 50%;
    background: var(--accent);
  }

  /* Back side */
  .card--back .wordmark {
    position: absolute; left: 150px; top: 130px;
    font-size: 44px;
  }
  .services {
    position: absolute; right: 150px; top: 238px;
    list-style: none; text-align: right;
    font-size: 17px; line-height: 22px; text-transform: uppercase;
    color: var(--muted);
  }
  .services li { display: flex; justify-content: flex-end; align-items: center; gap: 12px; }
  .services li::after {
    content: ""; width: 9px; height: 9px; border-radius: 50%;
    border: 2px solid var(--service-red);
  }

  /* Front side */
  .brand-mark {
    position: absolute; left: 50px; top: 70px;
    width: 230px; height: 230px; border-radius: 50%;
    background: var(--accent);
  }
  .card--front .wordmark {
    position: absolute; right: 40px; top: 40px;
    font-size: 38px;
  }
  .contact {
    position: absolute; right: 40px; top: 170px;
    text-align: right;
  }
  .contact__name {
    font-size: 28px; font-weight: 700; letter-spacing: 3px; text-transform: uppercase;
  }
  .contact__name span { color: var(--accent); }
  .contact__role { font-size: 17px; letter-spacing: 1px; margin-top: 2px; }
  .contact__rule {
    width: 58px; height: 2px; background: var(--accent);
    margin: 16px 0 14px auto;
  }
  .contact__list { list-style: none; font-size: 18px; line-height: 29px; letter-spacing: .5px; }
  .contact__list li { display: flex; justify-content: flex-end; align-items: center; gap: 12px; }
  .contact__list svg { width: 16px; height: 16px; }
  .contact__address { margin-right: 28px; }
</style>
</head>
<body>

<section class="card card--back" aria-label="Business card back">
  <div class="wordmark"><span class="wordmark__dot"></span>Kelvaro.ch</div>
  <ul class="services">
    <li>Vehicle labeling</li>
    <li>Shop window labeling</li>
    <li>Stickers and much more</li>
  </ul>
</section>

<section class="card card--front" aria-label="Business card front">
  <div class="brand-mark" role="img" aria-label="Brand symbol area in yellow"></div>
  <div class="wordmark">Kelvaro.ch</div>
  <div class="contact">
    <p class="contact__name">Mira <span>Lenhart</span></p>
    <p class="contact__role">Director</p>
    <div class="contact__rule"></div>
    <ul class="contact__list">
      <li>+41 ( 0 ) 79 482 6037
        <svg viewBox="0 0 16 16" fill="none" stroke="#fcc61a" stroke-width="1.6" stroke-linecap="round"><path d="M4 2l2 3-1.5 1.5a7 7 0 0 0 5 5L11 10l3 2-1 2.5C7.5 14.5 1.5 8.5 1.5 3z"/></svg>
      </li>
      <li>info@kelvaro-example.ch
        <svg viewBox="0 0 16 16" fill="none" stroke="#fcc61a" stroke-width="1.6"><rect x="1.5" y="3.5" width="13" height="9" rx="1"/><path d="M2 4l6 5 6-5"/></svg>
      </li>
      <li>www.Kelvaro-example.ch
        <svg viewBox="0 0 16 16" fill="none" stroke="#fcc61a" stroke-width="1.4"><circle cx="8" cy="8" r="6.5"/><ellipse cx="8" cy="8" rx="3" ry="6.5"/><path d="M1.5 8h13M2.5 5h11M2.5 11h11"/></svg>
      </li>
      <li class="contact__address">Lindenweg 14 9406 Tarnbach</li>
    </ul>
  </div>
</section>

</body>
</html>
```